Corwin Ashby College of Nursing website

Nursing college needs a fresh, streamlined website. Many of the items on our website are required by accreditation organizations.

```html
<!DOCTYPE html>
<html lang="en">
<head>
<meta charset="utf-8">
<title>Corwin Ashby College of Nursing</title>
<link href="https://fonts.googleapis.com/css2?family=Lora:wght@400;500;600;700&family=Noto+Sans:wght@400;500;600&display=swap" rel="stylesheet">
<style>
:root{
  --purple:#5b1a6c;
  --teal:#1c5f6f;
  --navy:#15496d;
  --green:#127260;
  --ink:#222222;
  --muted:#444444;
  --pale:#f1f5f9;
  --footer:#242122;
  --line:#dcdcdc;
}
*{box-sizing:border-box;margin:0;padding:0}
html,body{width:1200px;height:3377px;overflow:hidden;background:#fff}
body{position:relative;font-family:"Noto Sans",sans-serif;color:var(--ink)}
.abs{position:absolute}
.serif{font-family:"Lora",serif}
.btn{position:absolute;background:var(--purple);color:#fff;font-family:"Lora",serif;font-weight:600;font-size:16px;display:flex;align-items:center;justify-content:center;border-radius:2px}
.ph{position:absolute}

/* header */
.topstrip{left:0;top:0;width:1200px;height:8px;background:linear-gradient(90deg,var(--navy),var(--teal) 60%,var(--green))}
.nav a{position:absolute;top:46px;font-family:"Lora",serif;font-size:14px;color:var(--ink);text-decoration:none}
.nav a.active{color:var(--navy);text-decoration:underline}
.brand{left:496px;top:26px;display:flex;align-items:center;gap:10px}
.brand-mark{width:58px;height:58px;border-radius:50%;border:2px solid var(--navy)}
.brand-name{font-family:"Lora",serif;font-size:17px;line-height:22px;color:#444}

/* hero */
.hero-photo{left:0;top:102px;width:1200px;height:429px;background:linear-gradient(100deg,#4d78a6 0%,#30416c 40%,#4b2f7a 75%,#6a4aa0 100%)}
.hero-panel{left:0;top:374px;width:712px;height:275px;background:rgba(26,94,110,.94);color:#fff;padding:32px 0 0 112px}
.hero-panel .kicker{font-family:"Lora",serif;font-size:30px;line-height:36px}
.hero-panel h1{font-family:"Lora",serif;font-size:49px;line-height:50px;font-weight:700;margin-top:4px}
.hero-panel p{font-size:15.5px;line-height:28px;margin-top:12px;width:470px}
.badge{width:110px;height:110px;border-radius:50%;background:var(--navy);border:4px solid #1b2a44;top:539px}

/* successes */
.section-title{left:0;width:1200px;text-align:center;font-family:"Lora",serif;font-size:52px;color:var(--ink)}
.lead{left:0;width:1200px;text-align:center;font-size:16px;line-height:28px;color:var(--muted)}
.card{top:990px;width:302px;height:264px;background:#fff;box-shadow:0 1px 5px rgba(0,0,0,.18)}
.card .pic{position:absolute;left:0;top:0;width:302px;height:165px}
.card .icon{position:absolute;left:111px;top:124px;width:80px;height:80px;border-radius:50%;border:5px solid #fff;display:flex;align-items:center;justify-content:center}
.card .label{position:absolute;left:0;top:216px;width:302px;text-align:center;font-size:19px;font-weight:600}

/* mission */
.mission{left:0;top:1335px;width:1200px;height:575px;background:var(--pale)}
.mission h2{position:absolute;left:587px;top:76px;font-family:"Lora",serif;font-size:51px;line-height:54px;font-weight:400}
.mission p{position:absolute;left:588px;top:192px;width:505px;font-size:15.5px;line-height:28.4px;color:var(--muted)}

/* news */
.feature{left:112px;top:2079px;width:489px;height:406px;background:#f4f4f4}
.feature .pic{position:absolute;left:0;top:0;width:489px;height:227px}
.feature .date{position:absolute;right:0;top:24px;background:var(--green);color:#fff;font-size:15px;padding:4px 14px 5px}
.feature h3{position:absolute;left:13px;top:261px;width:420px;font-family:"Lora",serif;font-size:21px;line-height:28px;font-weight:500}
.feature p{position:absolute;left:13px;top:328px;width:470px;font-size:15.5px;line-height:26px;color:var(--muted)}
.item{left:634px;width:454px;height:102px}
.item .thumb{position:absolute;left:0;top:0;width:90px;height:102px;border:1px solid var(--line)}
.item h4{position:absolute;left:107px;top:10px;width:345px;font-family:"Lora",serif;font-size:17.5px;line-height:23px;font-weight:500}
.item .when{position:absolute;left:108px;font-size:15px;color:var(--muted)}
.divider{left:634px;width:454px;height:1px;background:var(--line)}

/* subscribe */
.subscribe{left:0;top:2548px;width:1200px;height:329px;background:linear-gradient(100deg,#136b62 0%,#155a6e 45%,#184a72 100%);color:#fff}
.subscribe h2{position:absolute;left:112px;top:60px;font-family:"Lora",serif;font-size:50px;font-weight:500}
.subscribe p{position:absolute;left:112px;top:133px;width:580px;font-size:15.5px;line-height:28.5px}
.subscribe .field{position:absolute;left:112px;top:219px;width:393px;height:41px;background:#fff;color:#555;font-size:15px;padding:10px 26px;border-radius:2px}

/* footer */
.footer{left:0;top:2877px;width:1200px;height:500px;background:var(--footer);color:#fff}
.footer h5{position:absolute;font-weight:400;font-size:14px;color:#9a9a9a;letter-spacing:.3px}
.footer ul{position:absolute;list-style:none;font-size:15px;line-height:30px}
.footer-brand{position:absolute;left:110px;top:60px;width:236px;height:236px;border-radius:50%;border:3px solid #fff;display:flex;align-items:center;justify-content:center;text-align:center;font-family:"Lora",serif;font-size:24px;line-height:32px}
.social{position:absolute;top:301px;width:31px;height:31px;border-radius:50%;border:1.5px solid #ddd}
.copyright{position:absolute;left:0;top:447px;width:1200px;text-align:center;font-size:15px}
</style>
</head>
<body>

<!-- header -->
<div class="abs topstrip"></div>
<nav class="nav">
  <a class="active" style="left:113px">Home</a>
  <a style="left:172px">About</a>
  <a style="left:232px">Academics</a>
  <a style="left:324px">Policies &amp; Handbooks</a>
  <a style="left:733px">Library</a>
  <a style="left:803px">Contact Us</a>
</nav>
<div class="abs brand">
  <div class="brand-mark"></div>
  <div class="brand-name">Corwin Ashby<br>College of Nursing</div>
</div>
<svg class="abs" style="left:902px;top:46px" width="18" height="18" viewBox="0 0 18 18"><circle cx="7.5" cy="7.5" r="5.5" fill="none" stroke="#222" stroke-width="1.8"/><line x1="11.5" y1="11.5" x2="16" y2="16" stroke="#222" stroke-width="1.8"/></svg>
<svg class="abs" style="left:942px;top:47px" width="21" height="16" viewBox="0 0 21 16"><rect y="0" width="21" height="2.6" fill="#222"/><rect y="6.5" width="21" height="2.6" fill="#222"/><rect y="13" width="21" height="2.6" fill="#222"/></svg>
<div class="btn" style="left:988px;top:35px;width:100px;height:41px">Donate</div>

<!-- hero -->
<div class="ph hero-photo" role="img" aria-label="Group of graduating nursing faculty and students in academic caps and gowns"></div>
<div class="abs hero-panel">
  <div class="kicker">Welcome to</div>
  <h1>Corwin Ashby College<br>of Nursing</h1>
  <p>Corwin Ashby College of Nursing has been educating nurses for over seventy years. Founded in 1945</p>
</div>
<div class="abs badge" style="left:809px" role="img" aria-label="Partner recognition badge"></div>
<div class="abs badge" style="left:943px" role="img" aria-label="College ranking badge"></div>

<!-- successes -->
<h2 class="abs section-title" style="top:752px">Our Successes</h2>
<p class="abs lead" style="top:821px">CACN is an independent single-purpose institution. Its mission is to provide a dynamic career-ladder<br>approach to nursing education to improve professional practice</p>
<div class="btn" style="left:528px;top:898px;width:145px;height:41px">Learn More</div>

<div class="abs card" style="left:112px">
  <div class="pic" role="img" aria-label="Nursing students and instructor in a clinical lab" style="background:linear-gradient(120deg,#8a7a62,#d8d6d2 55%,#3a3f55)"></div>
  <div class="icon" style="background:var(--navy)"><svg width="36" height="36" viewBox="0 0 36 36" fill="none" stroke="#fff" stroke-width="2.2"><rect x="8" y="5" width="20" height="26" rx="2"/><line x1="13" y1="13" x2="23" y2="13"/><line x1="13" y1="19" x2="23" y2="19"/><line x1="13" y1="25" x2="19" y2="25"/></svg></div>
  <div class="label">Apply Now</div>
</div>
<div class="abs card" style="left:449px">
  <div class="pic" role="img" aria-label="Group of nurses in scrubs" style="background:linear-gradient(120deg,#b9c7d4,#3d6da0 55%,#2c4f7e)"></div>
  <div class="icon" style="background:var(--green)"><svg width="38" height="38" viewBox="0 0 38 38" fill="none" stroke="#fff" stroke-width="2.2"><circle cx="19" cy="19" r="15"/><circle cx="19" cy="15" r="4"/><path d="M12 27c1.5-4 4-6 7-6s5.5 2 7 6"/></svg></div>
  <div class="label">Demographics</div>
</div>
<div class="abs card" style="left:786px">
  <div class="pic" role="img" aria-label="Graduates in blue gowns at commencement" style="background:linear-gradient(120deg,#2a3a8a,#4652b0 50%,#8aa0c8)"></div>
  <div class="icon" style="background:var(--purple)"><svg width="36" height="36" viewBox="0 0 36 36" fill="none" stroke="#fff" stroke-width="2.2"><circle cx="20" cy="12" r="7"/><line x1="20" y1="11" x2="20" y2="16"/><circle cx="20" cy="8" r=".8" fill="#fff"/><path d="M5 27h8l6 3 11-5"/></svg></div>
  <div class="label">Information</div>
</div>

<!-- mission -->
<section class="abs mission">
  <svg class="abs" style="left:86px;top:63px" width="460" height="460" viewBox="0 0 460 460">
    <path d="M20 230 A210 210 0 0 1 230 20" fill="none" stroke="var(--navy)" stroke-width="22"/>
    <path d="M230 20 A210 210 0 0 1 440 230" fill="none" stroke="var(--green)" stroke-width="22"/>
    <path d="M440 230 A210 210 0 0 1 230 440" fill="none" stroke="var(--purple)" stroke-width="22"/>
    <path d="M230 430 A200 200 0 0 1 30 230" fill="none" stroke="#231f20" stroke-width="14"/>
    <circle cx="230" cy="230" r="190" fill="#d9dde2" role="img" aria-label="Nursing instructor and student working with a microscope in a lab"/>
  </svg>
  <h2>Our Mission and<br>Vision</h2>
  <p>Corwin Ashby College of Nursing will be nationally recognized for excellence in nursing education, and noted for its comprehensive, innovative academic programs that are responsive to the healthcare challenges of the future.<br>Corwin Ashby College of Nursing is an independent single-purpose institution. Its mission is to provide a dynamic career-ladder approach to nursing education to improve professional practice and contribute to the health of communities.</p>
  <div class="btn" style="left:589px;top:439px;width:144px;height:41px">Learn More</div>
</section>

<!-- news -->
<h2 class="abs section-title" style="top:1968px">News &amp; Updates</h2>
<article class="abs feature">
  <div class="pic" role="img" aria-label="Simulation lab with patient manikins in hospital beds" style="background:linear-gradient(110deg,#7d7a78,#d8d3cc 50%,#a7a29b)"></div>
  <div class="date">Jul 5, 2024</div>
  <h3>NNAC Pre-accreditation Public Posting Notice</h3>
  <p>The Associate Degree in Nursing Program at Corwin Ashby College of Nursing is seeking pre-accreditation status from NNAC</p>
</article>

<div class="abs item" style="top:2079px">
  <div class="thumb" style="display:flex;align-items:center;justify-content:center"><div style="width:62px;height:62px;border-radius:50%;border:2px solid var(--navy)"></div></div>
  <h4>Public Notice of Upcoming Accreditation Review Visit by the ANEB</h4>
  <div class="when" style="top:70px">Jan 16, 2024</div>
</div>
<div class="abs divider" style="top:2205px"></div>
<div class="abs item" style="top:2232px">
  <div class="thumb" role="img" aria-label="Pre-entrance exams announcement flyer" style="background:linear-gradient(180deg,#e9b8c4,#f3d6dc)"></div>
  <h4>Now accepting pre-entrance exams!</h4>
  <div class="when" style="top:78px">Oct 31, 2023</div>
</div>
<div class="abs divider" style="top:2358px"></div>
<div class="abs item" style="top:2386px">
  <div class="thumb" role="img" aria-label="Hand writing with a pen on paper" style="background:linear-gradient(135deg,#c9cbcf,#6b6f78)"></div>
  <h4>Pre-admission Testing Schedule</h4>
  <div class="when" style="top:78px">Oct 29, 2023</div>
</div>

<!-- subscribe -->
<section class="abs subscribe">
  <h2>Subscribe to Us</h2>
  <p>Lorem ipsum dolor sit amet, consectetur adipiscing elit, sed do eius incididunt ut labore et dolore magna aliqua. Quis ipsum suspendisse ultrices gravida.</p>
  <div class="field">Email Address</div>
  <div class="btn" style="left:515px;top:219px;width:145px;height:41px">Learn More</div>
</section>

<!-- footer -->
<footer class="abs footer">
  <div class="footer-brand">Corwin Ashby<br>College of<br>Nursing</div>
  <h5 style="left:423px;top:66px">QUICK LINKS</h5>
  <ul style="left:423px;top:100px">
    <li>Office Suite</li><li>Course Lms</li><li>Student Portal</li><li>Email</li><li>Exam Testing</li><li>Proctor Service</li><li>Textbook Connect</li><li>Payroll (Employees Only)</li><li>Benefits Flex (Staff Only)</li><li>Records System</li>
  </ul>
  <h5 style="left:631px;top:66px">CONTACT US</h5>
  <ul style="left:631px;top:100px">
    <li>Transcript Request</li><li>Degree Verification Request</li><li>Employment</li><li>CACN Store</li>
  </ul>
  <h5 style="left:631px;top:260px">FOLLOW US</h5>
  <div class="social" style="left:630px"></div>
  <div class="social" style="left:668px"></div>
  <div class="social" style="left:706px"></div>
  <div class="social" style="left:744px"></div>
  <h5 style="left:867px;top:64px">LIBRARY</h5>
  <ul style="left:867px;top:98px">
    <li>About the Library</li><li>Library Catalog</li><li>Databases and Online Resources</li><li>Legal Sources of Online Content</li>
  </ul>
  <div class="btn" style="left:867px;top:264px;width:101px;height:41px">Donate</div>
  <div class="copyright">2024 Corwin Ashby College of Nursing. All Rights Reserved.</div>
</footer>

</body>
</html>
```